Roofing Company Modern look

I want a modern and sophisticated look for our roofing business.

Our address is :

5217 Mallow Creek Ln
Lakeview, Fl 32907

(407)-583-2196

www.HarborlineRoofsFl.com

I also want to make sure on the back there is a spot to put
Project Manager Name :

Number:

Because the cards will be used by all sales people

Project Manager Name :

Also there are accreditation we have logos are uploaded here as well that I would like maybe on the back of card as well

I also want to highlight our special attributions or trades:

Residential & Commercial
Fully Insured
License # CCC7482913
Insurance Claims
Serving Central Florida Since 1992
Free Estimates

Contact Information for Business Card

Our address is :

5217 Mallow Creek Ln
Lakeview, Fl 32907

(407)-583-2196

Project Manager Name :

Residential & Commercial
Fully Insured
License # CCC7482913
Insurance Claims
Free Estimates

Font styles to use
Serif
Sans Serif

Colors
3176b5

Requirements
Must have
• Must have royal blue like my logo grey and black are the colors I like

```html
<!DOCTYPE html>
<html lang="en">
<head>
<meta charset="utf-8">
<title>Harborline Roofs &amp; Gutters – Business Card</title>
<link href="https://fonts.googleapis.com/css2?family=Source+Sans+3:wght@400;600;700&display=swap" rel="stylesheet">
<style>
  :root {
    --royal: #225ca8;
    --royal-light: #2a6ab5;
    --charcoal: #4a4b4f;
    --paper: #f4f4f4;
    --ink: #3c3d40;
    --backdrop: #e4e4e4;
    --white: #ffffff;
  }
  * { margin: 0; padding: 0; box-sizing: border-box; }
  html, body { width: 1200px; height: 960px; overflow: hidden; }
  body {
    background: var(--backdrop);
    font-family: "Source Sans 3", "Source Sans Pro", Arial, sans-serif;
    position: relative;
  }
  .card {
    position: absolute;
    left: 307px;
    width: 593px;
    overflow: hidden;
  }

  /* Front */
  .card-front { top: 127px; height: 337px; background: var(--royal); }
  .region-map {
    position: absolute; left: 220px; top: 0; width: 360px; height: 305px;
    background: radial-gradient(ellipse at 65% 45%, rgba(52,118,190,0.75) 0%, rgba(42,106,181,0.4) 50%, rgba(34,92,168,0) 75%);
  }
  .front-brand {
    position: absolute; left: 0; right: 0; top: 60px;
    text-align: center; color: var(--white); font-weight: 600;
  }
  .brand-dot {
    width: 62px; height: 62px; border-radius: 50%;
    background: var(--white); margin: 0 auto 30px;
  }
  .brand-name { font-size: 42px; letter-spacing: 3.5px; line-height: 1; }
  .brand-sub { font-size: 14px; letter-spacing: 1.8px; margin-top: 4px; }
  .front-tagline {
    position: absolute; left: 0; right: 0; top: 249px;
    text-align: center; color: var(--white);
    font-weight: 600; font-size: 16px; line-height: 20px;
  }
  .front-strip {
    position: absolute; left: 0; right: 0; bottom: 0; height: 28px;
    background: var(--charcoal); color: var(--white);
    text-align: center; font-size: 16px; line-height: 28px; letter-spacing: 0.2px;
  }

  /* Back */
  .card-back { top: 518px; height: 338px; background: var(--paper); }
  .back-brand {
    position: absolute; left: 40px; top: 40px; width: 220px;
    text-align: center; color: var(--royal); font-weight: 600;
  }
  .back-brand .brand-dot { width: 56px; height: 56px; background: var(--royal); margin-bottom: 28px; }
  .back-brand .brand-name { font-size: 30px; letter-spacing: 2.5px; }
  .back-brand .brand-sub { font-size: 11px; letter-spacing: 1.3px; margin-top: 3px; color: var(--ink); }

  .accreditations { position: absolute; left: 330px; top: 35px; width: 220px; height: 55px; }
  .badge { position: absolute; }
  .badge-rect { left: 0; top: 14px; width: 95px; height: 27px; background: #fff; border: 2px solid #c22a2a; }
  .badge-tall { left: 114px; top: 0; width: 33px; height: 53px; background: #fff; border: 2px solid var(--royal); border-radius: 3px; }
  .badge-hex { left: 166px; top: 3px; }

  .contact {
    position: absolute; right: 44px; top: 180px;
    text-align: right; color: var(--ink); font-size: 16px; line-height: 20px;
  }
  .contact .address { margin-bottom: 8px; }
  .contact-line { display: flex; justify-content: flex-end; align-items: center; gap: 5px; }
  .contact-line svg { width: 14px; height: 14px; fill: var(--royal); }

  .person { position: absolute; left: 43px; top: 246px; }
  .person-name { color: var(--royal); font-size: 20px; font-weight: 600; letter-spacing: 0.3px; line-height: 22px; }
  .person-title { color: var(--ink); font-size: 16px; line-height: 20px; margin-top: 1px; }

  .back-strip { position: absolute; left: 0; right: 0; bottom: 0; height: 30px; }
  .back-strip svg { position: absolute; inset: 0; }
  .license, .website {
    position: absolute; top: 0; line-height: 30px; color: var(--white); font-size: 16px;
  }
  .license { left: 43px; }
  .website { right: 38px; }
</style>
</head>
<body>

<section class="card card-front" aria-label="Business card front">
  <div class="region-map" role="img" aria-label="Faint map of Florida"></div>
  <div class="front-brand">
    <div class="brand-dot"></div>
    <div class="brand-name">HARBORLINE</div>
    <div class="brand-sub">ROOFS &amp; GUTTERS INC.</div>
  </div>
  <p class="front-tagline">RESIDENTIAL &amp; COMMERCIAL<br>Serving Central Florida Since 1992</p>
  <div class="front-strip">FULLY INSURED • INSURANCE CLAIMS • FREE ESTIMATES</div>
</section>

<section class="card card-back" aria-label="Business card back">
  <div class="back-brand">
    <div class="brand-dot"></div>
    <div class="brand-name">HARBORLINE</div>
    <div class="brand-sub">ROOFS &amp; GUTTERS INC.</div>
  </div>

  <div class="accreditations" aria-label="Accreditation badges">
    <div class="badge badge-rect"></div>
    <div class="badge badge-tall"></div>
    <svg class="badge badge-hex" width="54" height="48" viewBox="0 0 54 48">
      <polygon points="14,1 40,1 53,24 40,47 14,47 1,24" fill="#2f3033"/>
      <polygon points="17,7 37,7 47,24 37,41 17,41 7,24" fill="#e8e8e8"/>
    </svg>
  </div>

  <div class="contact">
    <div class="address">5217 Mallow Creek Ln<br>Lakeview, Fl 32907</div>
    <div class="contact-line">(407) 583-2196
      <svg viewBox="0 0 16 16"><path d="M4 0h8a1 1 0 0 1 1 1v14a1 1 0 0 1-1 1H4a1 1 0 0 1-1-1V1a1 1 0 0 1 1-1zm1 2v10h6V2zm3 11a1 1 0 1 0 0 2 1 1 0 0 0 0-2z"/></svg>
    </div>
    <div class="contact-line">(407) 583-2196
      <svg viewBox="0 0 16 16"><path d="M3.6 1.2 5.8 0.6l1.6 3.6-1.5 1.2c.8 1.8 2.2 3.2 4 4l1.2-1.5 3.6 1.6-.6 2.2c-.2.8-1 1.3-1.8 1.2C6.7 12.4 2.6 8.3 2.1 2.9c-.1-.8.4-1.5 1.5-1.7z"/></svg>
    </div>
    <div class="contact-line">daniel@HarborlineRoofsFl.com
      <svg viewBox="0 0 16 16"><path d="M1 3h14v10H1zm1.5 1.5v.3L8 8.6l5.5-3.8v-.3zm0 2.1v4.9h11V6.6L8 10.4z"/></svg>
    </div>
  </div>

  <div class="person">
    <div class="person-name">DANIEL CARVER</div>
    <div class="person-title">Project Manager</div>
  </div>

  <div class="back-strip">
    <svg width="593" height="30" viewBox="0 0 593 30" preserveAspectRatio="none">
      <polygon points="0,0 330,0 318,30 0,30" fill="var(--charcoal)"/>
      <polygon points="334,0 593,0 593,30 322,30" fill="var(--royal)"/>
    </svg>
    <span class="license">License # CCC7482913</span>
    <span class="website">www.HarborlineRoofsFl.com</span>
  </div>
</section>

</body>
</html>
```